Hartwell Estates Business Cards

I would like a business card that includes myself and my partner.
Includes: Logo, office #, email, website, our names, our numbers and possibly the address. I would also like the logo to be embossed and the card to be horizontal.
There is a photo of our yard signs to give you an idea of the colors of our business.

Target Market(s)

Everyone in real estate market.
We are in a rural area. Our clientele are from all socioeconomic backgrounds.

Industry/Entity Type

Real Estate Agent

Contact Information for Business Card

Company Name: Hartwell Estates
Our Names, Titles & Cell #'s : Dana Pembrook-Broker (555).317.6624, Marla Pembrook-Realtor (555).609.1385
Office #: (555).240.3918
Website: hartwellestates-demo.com
Joint Email: pembrook@hartwellestates-demo.com
Office Address: 418B W. Calloway Ave.
Millbrook, OR. 70913

Font styles to use
Serif

Requirements
Must have
• HORIZONTAL, Logo, Myself and my partners names, Our cell #'s, our office #, our website, our email address
Nice to have
• Embossed logo, office address, our titles.

```html
<!DOCTYPE html>
<html lang="en">
<head>
<meta charset="utf-8">
<title>Hartwell Estates Business Cards</title>
<link rel="stylesheet" href="https://fonts.googleapis.com/css2?family=PT+Sans:wght@400;700&display=swap">
<style>
  :root {
    --backdrop: #3b3430;
    --card-black: #1d1c1f;
    --card-black-soft: #262428;
    --brand-purple: #4b2474;
    --name-purple: #6a3596;
    --text-light: #ecebef;
    --font-text: "PT Sans", sans-serif;
  }
  * { box-sizing: border-box; margin: 0; padding: 0; }
  html, body {
    width: 1200px;
    height: 844px;
    overflow: hidden;
    background: var(--backdrop);
  }
  .card-sheet {
    position: relative;
    width: 1200px;
    height: 844px;
  }
  .card {
    position: absolute;
    top: 272px;
    width: 525px;
    height: 300px;
    background: radial-gradient(ellipse at 30% 30%, var(--card-black-soft), var(--card-black) 70%);
    box-shadow: 0 10px 24px rgba(0,0,0,0.45);
    overflow: hidden;
    font-family: var(--font-text);
  }
  .card--contact { left: 50px; }
  .card--brand { left: 625px; }

  /* contact side */
  .contact-mark {
    position: absolute;
    left: 40px;
    top: 92px;
    width: 170px;
    display: flex;
    align-items: center;
    gap: 10px;
  }
  .mark-square {
    flex: none;
    width: 14px;
    height: 14px;
    background: var(--brand-purple);
  }
  .mark-name {
    color: var(--name-purple);
    font-weight: 700;
    font-size: 24px;
    line-height: 1.05;
  }
  .contact-details {
    position: absolute;
    left: 250px;
    top: 28px;
    color: var(--text-light);
    font-size: 14px;
    line-height: 19px;
  }
  .person + .person { margin-top: 6px; }
  .person-name {
    color: var(--name-purple);
    font-weight: 700;
    font-size: 16px;
  }
  .office-lines { margin-top: 6px; }
  .office-line {
    display: flex;
    align-items: center;
    gap: 7px;
  }
  .office-bullet {
    width: 8px;
    height: 8px;
    background: var(--brand-purple);
  }
  .address-band {
    position: absolute;
    left: 0;
    right: 0;
    bottom: 0;
    height: 70px;
    background: var(--brand-purple);
    color: var(--text-light);
    font-size: 15px;
    display: flex;
    align-items: center;
    padding-left: 130px;
  }

  /* brand side */
  .brand-block {
    position: absolute;
    left: 90px;
    top: 95px;
    display: flex;
    align-items: center;
    gap: 16px;
  }
  .brand-square {
    width: 20px;
    height: 20px;
    background: var(--brand-purple);
  }
  .brand-name {
    color: var(--brand-purple);
    font-weight: 700;
    font-size: 40px;
    line-height: 1;
  }
  .brand-rule {
    position: absolute;
    left: 216px;
    top: 152px;
    width: 220px;
    height: 1px;
    background: var(--brand-purple);
  }
  .brand-web {
    position: absolute;
    left: 262px;
    top: 168px;
    color: var(--brand-purple);
    font-size: 13px;
    font-weight: 700;
  }
</style>
</head>
<body>
<main class="card-sheet">
  <section class="card card--contact" aria-label="Contact side">
    <div class="contact-mark">
      <span class="mark-square"></span>
      <span class="mark-name">Hartwell Estates</span>
    </div>
    <div class="contact-details">
      <div class="person">
        <div class="person-name">Dana Pembrook</div>
        <div class="person-title">Broker</div>
        <div class="person-phone">(555).317.6624</div>
      </div>
      <div class="person">
        <div class="person-name">Marla Pembrook</div>
        <div class="person-title">Realtor</div>
        <div class="person-phone">(555).609.1385</div>
      </div>
      <div class="office-lines">
        <div class="office-line"><span class="office-bullet"></span>(555).240.3918</div>
        <div class="office-line"><span class="office-bullet"></span>pembrook@hartwellestates-demo.com</div>
      </div>
    </div>
    <div class="address-band">418B W. Calloway Ave.&nbsp; Millbrook, OR. 70913</div>
  </section>

  <section class="card card--brand" aria-label="Brand side">
    <div class="brand-block">
      <span class="brand-square"></span>
      <span class="brand-name">Hartwell Estates</span>
    </div>
    <div class="brand-rule"></div>
    <div class="brand-web">www.hartwellestates-demo.com</div>
  </section>
</main>
</body>
</html>
```